New business card for a regional office of a US M&A company

We need business card for a finance company, office based in Hong Kong , our Head office is in US, our business is to Merge and acquires companies , the new office will be a regional office for the Asia Pacific region. We want to use the head office logo as attached ( but don't have to be exactly the same, can be a variation to it) as a base and then add Asia Pacific alongside the logo.
We would prefer to have be bilingual Eng + Chinese, although we don't really have Chinese company name .

Industry/Entity Type

Business

Contact Information for Business Card

Clara Jo Tsang
 

VP,
APAC M&A Operations
Orin Vantage Asia Pacific Limited
 
Unit 1407, K18
18 Tai Lok Shan Road, 
Hong Kong 
 
M: +852 6038 1742
T : +852 2836 4100
F : +852 2836 4177
VOIP: 4158
 
cjtsang@orinvantage.com

Font styles to use
Serif
Sans Serif

Colors

Designer to choose colors to be used in the design.

Requirements
Must have
• APAC Office

```html
<!DOCTYPE html>
<html lang="en">
<head>
<meta charset="utf-8">
<title>Orin Vantage Asia Pacific – Business Card</title>
<link href="https://fonts.googleapis.com/css2?family=Libre+Baskerville&family=Montserrat:wght@400;600;700&display=swap" rel="stylesheet">
<style>
  :root {
    --navy: #0d2a47;
    --cyan: #1fa3c9;
    --ink: #3a3a3a;
    --card: #f7f7f7;
    --map: #e3e4e6;
    --stage: #3a3a3a;
    --rule: #9a9a9a;
  }
  * { box-sizing: border-box; margin: 0; padding: 0; }
  html, body { width: 1200px; height: 834px; overflow: hidden; }
  body {
    background: var(--stage);
    font-family: "Montserrat", sans-serif;
    color: var(--ink);
    position: relative;
  }
  .card {
    position: absolute;
    width: 540px;
    height: 308px;
    background: var(--card);
    overflow: hidden;
  }
  .card--front { left: 40px; top: 110px; }
  .card--back { left: 620px; top: 416px; background: linear-gradient(135deg, #fbfbfb, #ececec); }

  .world-map {
    position: absolute;
    inset: 20px 30px;
    background: radial-gradient(ellipse at 50% 50%, var(--map) 0%, #eeeff0 60%, var(--card) 100%);
    border-radius: 8px;
  }

  .brand-block {
    position: absolute;
    background: var(--navy);
    border-bottom: 4px solid var(--cyan);
    display: flex;
    flex-direction: column;
    align-items: center;
    justify-content: center;
    gap: 10px;
  }
  .card--front .brand-block { left: 182px; top: 92px; width: 176px; height: 110px; }
  .card--back .brand-block { right: 40px; top: 0; width: 176px; height: 104px; }
  .brand-mark {
    width: 20px; height: 20px;
    background: #e9edf1;
  }
  .brand-name {
    color: var(--cyan);
    font-weight: 700;
    font-size: 17px;
    letter-spacing: 0.5px;
  }

  .contact { position: absolute; left: 58px; top: 86px; }
  .contact__name {
    font-family: "Libre Baskerville", serif;
    font-size: 17px;
    line-height: 22px;
    color: var(--ink);
  }
  .contact__title { font-size: 12px; line-height: 16px; color: var(--cyan); margin-top: 2px; }
  .rule { width: 30px; height: 1px; background: var(--rule); margin: 10px 0 7px; }
  .phones { list-style: none; font-size: 11px; line-height: 15px; }
  .phones li { display: flex; align-items: center; gap: 10px; }
  .phones svg { width: 10px; height: 10px; fill: none; stroke: var(--cyan); stroke-width: 1.4; }
  .phones .voip { padding-left: 20px; }
  .company { font-size: 11px; line-height: 15px; }
  .company__name { color: var(--cyan); font-weight: 600; }

  .accent-bar {
    position: absolute;
    right: 40px;
    top: 250px;
    width: 170px;
    height: 22px;
    background: var(--navy);
    border-top: 3px solid var(--cyan);
  }
</style>
</head>
<body>
  <section class="card card--front">
    <div class="world-map" role="img" aria-label="Faint dotted world map background"></div>
    <div class="brand-block">
      <span class="brand-mark"></span>
      <span class="brand-name">ORIN VANTAGE</span>
    </div>
  </section>

  <section class="card card--back">
    <div class="brand-block">
      <span class="brand-mark"></span>
      <span class="brand-name">ORIN VANTAGE</span>
    </div>

    <div class="contact">
      <p class="contact__name">Clara Jo Tsang</p>
      <p class="contact__title">VP, APAC M&amp;A Operations</p>
      <div class="rule"></div>
      <ul class="phones">
        <li><svg viewBox="0 0 10 10"><rect x="2.5" y="0.8" width="5" height="8.4" rx="1"/></svg>+852 6038 1742</li>
        <li><svg viewBox="0 0 10 10"><path d="M2 1l2 2-1 1.3c.6 1.2 1.5 2.1 2.7 2.7L7 6l2 2-1.2 1.2C4.5 9 1 5.5.8 2.2z"/></svg>+852 2836 4100</li>
        <li><svg viewBox="0 0 10 10"><rect x="1" y="4" width="8" height="4.5"/><rect x="2.5" y="1" width="5" height="3"/></svg>+852 2836 4177</li>
        <li class="voip">VOIP 4158</li>
      </ul>
      <div class="rule"></div>
      <div class="company">
        <p class="company__name">Orin Vantage Asia Pacific Limited</p>
        <p>Unit 1407, K18</p>
        <p>18 Tai Lok Shan Road,</p>
        <p>Hong Kong</p>
      </div>
    </div>

    <div class="accent-bar"></div>
  </section>
</body>
</html>
```